New Business Card for Web Design/Internet Marketing Company

Looking for a great looking new business card. We are a 10 year old web design, internet marketing and website management company that works mostly with small businesses.

Our new card needs to better match the colors and style of our website, be bold, extremely usable and slightly edgy.

Target Market(s)

Small/Medium businesses that have websites

Industry/Entity Type

Internet

Requirements
Must have
• Front and back design, full color, rounded corners please

Must use the colors/style of our website (JPG provided)

INFO FOR CARDS (as readable as possible please)
Mark Lenner
President/CEO
mark@trelvanmedia.example
Phone: 520-381-7459
Toll Free: 866-381-7459
Address: 4315 W. Calloway Ave. Ste. 140, Tucson, AZ 85792

THINGS I WANT TO PROMOTE (if there is room):
1. Our Website - www.trelvanmedia.example

2. Social Media
Twitter: @trelvanmedia
Facebook: www.facebook.com/trelvanmedia

3. Our Services
Web Design
Internet Marketing
Website Management

```html
<!DOCTYPE html>
<html lang="en">
<head>
<meta charset="utf-8">
<title>Trelvan Media – Business Card</title>
<link href="https://fonts.googleapis.com/css2?family=Open+Sans:ital,wght@0,400;0,600;0,700;1,400&display=swap" rel="stylesheet">
<style>
  :root {
    --navy: #1c2a7d;
    --navy-light: #2f47a8;
    --orange: #f07f1f;
    --sky: #2d8fd0;
    --ink: #2a2a2a;
    --paper: #ffffff;
    --backdrop: #e6e7ea;
  }
  * { box-sizing: border-box; margin: 0; padding: 0; }
  html, body {
    width: 1200px; height: 944px; overflow: hidden;
    background: var(--backdrop);
    font-family: "Open Sans", Arial, sans-serif;
  }
  .canvas { position: relative; width: 1200px; height: 944px; }
  .card {
    position: absolute; width: 560px; height: 320px;
    border-radius: 22px; overflow: hidden;
    box-shadow: 0 10px 24px rgba(0,0,0,.18);
  }
  /* Front */
  .card--front {
    left: 60px; top: 90px;
    background: radial-gradient(circle at 45% 35%, var(--navy-light), var(--navy) 75%);
  }
  .brand { position: absolute; display: flex; align-items: center; gap: 14px; }
  .brand__dot { width: 58px; height: 58px; border-radius: 50%; background: var(--orange); }
  .brand__name { font-size: 44px; font-weight: 600; letter-spacing: -0.5px; line-height: 1; }
  .brand__tagline {
    position: absolute; font-size: 15px; font-weight: 600; color: var(--orange); white-space: nowrap;
  }
  .card--front .brand { left: 58px; top: 92px; }
  .card--front .brand__name { color: var(--paper); }
  .card--front .brand__tagline { left: 360px; top: 158px; }
  .front__url {
    position: absolute; left: 0; right: 0; top: 222px;
    text-align: center; color: var(--paper); font-size: 15px; font-weight: 600; letter-spacing: .3px;
  }
  .services {
    position: absolute; left: 0; right: 0; bottom: 0; height: 54px;
    background: var(--orange); color: var(--paper);
    display: flex; align-items: center; justify-content: center; gap: 10px;
    font-size: 15px; font-weight: 600;
  }
  .services__sep { width: 5px; height: 5px; background: var(--paper); border-radius: 50%; }
  /* Back */
  .card--back { left: 580px; top: 520px; background: var(--paper); }
  .card--back .brand { left: 160px; top: 34px; }
  .card--back .brand__dot { width: 50px; height: 50px; }
  .card--back .brand__name { color: var(--sky); font-size: 38px; }
  .card--back .brand__tagline { left: 402px; top: 92px; }
  .person { position: absolute; left: 36px; top: 140px; }
  .person__name { font-size: 21px; color: var(--ink); font-weight: 400; }
  .person__title { font-size: 13px; color: var(--orange); font-style: italic; margin-top: 2px; }
  .address {
    position: absolute; left: 36px; top: 208px; display: flex; gap: 10px;
    font-size: 13px; color: var(--ink); line-height: 1.45;
  }
  .contacts { position: absolute; left: 296px; top: 146px; list-style: none; }
  .contacts li {
    display: flex; align-items: center; gap: 9px;
    font-size: 13px; color: var(--ink); line-height: 21px; white-space: nowrap;
  }
  .contacts svg, .address svg { flex: none; }
  .contacts__link b { color: var(--orange); font-weight: 400; }
  .icon-mark { width: 13px; height: 13px; background: var(--navy); border-radius: 2px; flex: none; }
  .icon-mark--round { border-radius: 50%; }
  .back__band {
    position: absolute; left: 0; right: 0; bottom: 0; height: 30px;
    background: linear-gradient(90deg, var(--navy), var(--navy-light));
    border-top: 4px solid var(--orange);
  }
</style>
</head>
<body>
<main class="canvas">

  <section class="card card--front" aria-label="Card front">
    <div class="brand">
      <span class="brand__dot"></span>
      <span class="brand__name">trelvanmedia</span>
    </div>
    <span class="brand__tagline">Build your Web</span>
    <p class="front__url">www.trelvanmedia.example</p>
    <div class="services">
      <span>Web Design</span><span class="services__sep"></span>
      <span>Internet Marketing</span><span class="services__sep"></span>
      <span>Website Management</span>
    </div>
  </section>

  <section class="card card--back" aria-label="Card back">
    <div class="brand">
      <span class="brand__dot"></span>
      <span class="brand__name">trelvanmedia</span>
    </div>
    <span class="brand__tagline">Build your Web</span>

    <div class="person">
      <p class="person__name">Mark Lenner</p>
      <p class="person__title">President/CEO</p>
    </div>

    <div class="address">
      <svg width="14" height="14" viewBox="0 0 14 14" aria-hidden="true">
        <path d="M7 1 L13 7 H11 V13 H8.5 V9 H5.5 V13 H3 V7 H1 Z" fill="var(--navy)"/>
      </svg>
      <p>4315 W. Calloway Ave. Ste. 140<br>Tucson, AZ 85792</p>
    </div>

    <ul class="contacts">
      <li>
        <svg width="13" height="13" viewBox="0 0 14 14" aria-hidden="true">
          <rect x="1" y="3" width="12" height="9" rx="1" fill="var(--navy)"/>
          <path d="M1.5 3.5 L7 8 L12.5 3.5" stroke="#fff" stroke-width="1.2" fill="none"/>
        </svg>
        mark@trelvanmedia.example
      </li>
      <li>
        <svg width="13" height="13" viewBox="0 0 14 14" aria-hidden="true">
          <path d="M3 1 L5.5 1 L6.5 4.5 L5 5.8 C5.8 7.6 6.6 8.4 8.2 9 L9.5 7.5 L13 8.5 L13 11 C13 12 12 13 11 13 C5.5 12.5 1.5 8.5 1 3 C1 2 2 1 3 1 Z" fill="var(--navy)"/>
        </svg>
        520-381-7459
      </li>
      <li>
        <svg width="13" height="13" viewBox="0 0 14 14" aria-hidden="true">
          <path d="M3 1 L5.5 1 L6.5 4.5 L5 5.8 C5.8 7.6 6.6 8.4 8.2 9 L9.5 7.5 L13 8.5 L13 11 C13 12 12 13 11 13 C5.5 12.5 1.5 8.5 1 3 C1 2 2 1 3 1 Z" fill="var(--navy)"/>
        </svg>
        866-381-7459 (toll free)
      </li>
      <li><span class="icon-mark icon-mark--round"></span>@trelvanmedia</li>
      <li><span class="icon-mark"></span><span class="contacts__link">www.<b>linkvane.example</b>/trelvanmedia</span></li>
    </ul>

    <div class="back__band"></div>
  </section>

</main>
</body>
</html>
```